Professional Engineering Web Design

Project Brief: Website Redesign for Mechanical Design Consultancy
Project Overview
I want to update and improve my current website to create a more professional, modern, and high-credibility online presence for my mechanical design consultancy.

Current site: https://valtorix.design/

The new website must communicate expertise, precision, and trust—matching the standard of top engineering and product design agencies.

Reference Websites (Style + Structure Inspiration)
These represent the quality, cleanliness, and professionalism I want to achieve:

https://plinthwaredesign.com/
https://www.sorvane.com/
https://bramlow-uk.com/
Brand Look
Professional, modern, engineering-focused aesthetic
Clean layouts and strong typography
High-quality imagery conveying precision, innovation, and mechanical expertise
Colour scheme and styling must follow my existing logo (attached in project)
Platform Requirements
The website must be built on WordPress
Should use a clean, flexible theme or modern page builder (Elementor, Gutenberg, Bricks, or similar)
Avoid overly complex custom coding so I can easily edit content later
Final deliverable must allow me to manage and update content without developer assistance
Functionality
Fast-loading, lightweight, and smooth user experience
Clean animations and transitions similar to the reference sites
Fully mobile responsive
Clear navigation and strong visual hierarchy
Contact forms optimised for lead generation
Optional: subtle scroll effects, case study sliders, icon animations, etc.
SEO Aspirations
Developer should recommend and implement a modern SEO strategy
Proper on-page SEO setup (titles, meta, schema, alt tags, heading structure)
Optimised site architecture for ranking and crawling
Aim: Generate leads through improved visibility and keyword targeting
Optional but useful: Google Analytics, Google Search Console setup
User Journeys
(Recommended structure)

The site should be crafted around clear, intuitive journeys for each type of visitor:

Potential new clients
Quickly understand what services I offer
View examples of past work / case studies
See credibility indicators (process, expertise, industries served)
Easily contact me or request a project discussion
Returning clients
Access updated portfolio items
Find contact details or book follow-up work easily
General visitors discovering through SEO
Be guided to valtorix service areas
Understand my value proposition quickly
Be invited to learn more or make contact
The developer should design the structure to support these journeys smoothly.

Maintenance Expectations
Website will be maintained by me, so it should be easy to update using relatively basic WordPress skills
Use modular templates and simple backend structure
Avoid unnecessary plugins
Provide brief handover documentation if required
Hosting Preferences
Site is currently hosted via a family member
Open to discussing moving to a paid, reliable hosting provider if preferable for performance and maintainability
Developer may advise on the best hosting setup for WordPress
Content
Most content can be taken from the existing website
Developer is welcome to suggest improvements to structure, layout, and imagery
Must remain easy for me to edit or add new content later (e.g., new projects)
Deliverables
Fully built WordPress website
Clean, professional, modern design inspired by the reference sites
Mobile-responsive across all devices
SEO-ready structure and optimisations
Transfer of website and admin rights
Any design assets, templates, or documentation used

```html
<!DOCTYPE html>
<html lang="en">
<head>
<meta charset="utf-8">
<title>Valtorix Mechanical Design</title>
<link rel="stylesheet" href="https://fonts.googleapis.com/css2?family=Urbanist:wght@400;500;600;700;800&display=swap">
<style>
:root{
  --blue:#3461f0;
  --blue-dark:#2448d6;
  --ink:#141821;
  --text:#3b3f4a;
  --muted:#8a8f9a;
  --grey:#f2f2f3;
  --line:#dfe3ea;
  --white:#fff;
  --dark:#2b2f36;
}
*{box-sizing:border-box;margin:0;padding:0}
html,body{width:1200px;height:4559px;overflow:hidden}
body{font-family:"Urbanist",sans-serif;color:var(--text);background:var(--white);position:relative}
.section{position:absolute;left:0;width:1200px}
.abs{position:absolute}
h1,h2,h3{font-family:"Urbanist",sans-serif;color:var(--ink);font-weight:800}
.eyebrow{color:var(--blue);font-size:17px;font-weight:600;letter-spacing:.3px}
.title{font-size:32px;font-weight:800;text-transform:uppercase;color:var(--ink);letter-spacing:-.3px}
.center{text-align:center;width:1200px;left:0}
.btn{display:inline-flex;align-items:center;justify-content:center;background:var(--blue);color:#fff;border-radius:24px;font-size:13px;font-weight:700;text-transform:uppercase;letter-spacing:.3px}
p{font-size:13.5px;line-height:24px}

/* top bar */
.topbar{top:0;height:28px;background:var(--blue);color:#dfe6ff;font-size:12px;display:flex;justify-content:center;align-items:center;gap:54px}
.topbar span{display:flex;align-items:center;gap:8px}
.topbar b{color:#fff;font-weight:500}
/* header */
.header{top:28px;height:78px;background:#fff;border-bottom:1px solid #eee}
.brand{display:flex;align-items:center;gap:10px}
.brand-dot{width:52px;height:52px;border-radius:50%;background:var(--blue)}
.brand-name{font-size:30px;font-weight:700;color:var(--dark);letter-spacing:3px;line-height:1}
.brand-sub{font-size:8.5px;font-weight:700;color:var(--blue);letter-spacing:1.4px;margin-top:3px}
.nav{left:467px;top:30px;display:flex;gap:24px;font-size:12.5px;color:var(--muted)}
.nav .active{color:var(--ink);font-weight:600;border-bottom:2px solid var(--blue);padding-bottom:5px}
.search{left:812px;top:22px;height:34px;border-left:1px solid var(--line);padding-left:28px;display:flex;align-items:center;gap:8px;font-size:12.5px;color:var(--muted)}
.contact-btn{left:932px;top:21px;width:127px;height:36px;background:var(--dark);color:#fff;border-radius:20px;display:flex;align-items:center;justify-content:space-between;padding:0 4px 0 18px;font-size:12.5px}
.ring{width:28px;height:28px;border-radius:50%;background:#fff;display:flex;align-items:center;justify-content:center}
/* hero */
.hero{top:106px;height:660px;overflow:hidden}
.hero-img{top:0;left:0;width:1200px;height:660px;background:linear-gradient(100deg,#1d2026 0%,#2d3138 38%,#4a5562 62%,#6b5d50 82%,#3a3530 100%)}
.hero-frame{left:104px;top:84px;width:80px;height:200px;border:2px solid rgba(255,255,255,.8);border-right:none;border-radius:18px 0 0 18px}
.hero h1{position:absolute;left:142px;top:112px;color:#fff;font-size:54px;line-height:72px;letter-spacing:.5px}
.hero .lead{left:142px;top:254px;color:#fff;font-size:16px;line-height:30px;font-weight:500}
.hero .btn{left:142px;top:380px;height:44px;width:192px;text-transform:none;font-weight:500;font-size:13.5px;justify-content:space-between;padding:0 6px 0 26px}
/* about */
.about-img{left:142px;top:811px;width:433px;height:433px;border-radius:50%;background:radial-gradient(circle at 45% 50%,#eef1f7 0%,#b8c3dc 40%,#4d6de0 75%,#2b46b5 100%)}
.about-text{left:648px;top:836px;width:420px}
.about-text .title{margin:6px 0 18px;font-size:28px;white-space:nowrap}
.about-text p{margin-bottom:12px}
/* expertise */
.expertise{top:1336px;height:606px;background:var(--grey)}
.card{width:288px;height:340px;background:#fff;border-radius:6px;top:174px;box-shadow:0 6px 20px rgba(20,30,60,.06);text-align:center}
.card-inner{position:absolute;inset:10px;border:1px solid var(--line);border-radius:6px}
.card.featured .card-inner{border-color:#8aa3f2}
.icon-c{width:98px;height:98px;border-radius:50%;background:#dfe6fb;margin:32px auto 22px;display:flex;align-items:center;justify-content:center}
.featured .icon-c{background:var(--blue)}
.card h3{font-size:22px;line-height:27px;font-weight:700}
.card p{margin-top:10px;font-size:14px;line-height:26px;padding:0 24px}
/* portfolio */
.slide{border-radius:8px}
/* about me */
.aboutme{top:2650px;height:594px;background:var(--grey)}
/* testimonials */
.testimonials{top:3244px;height:600px}
.quote-card{left:283px;top:198px;width:634px;height:293px;background:#fff;box-shadow:0 8px 28px rgba(20,30,60,.1);text-align:center;padding-top:46px}
.quote-text{font-size:13.5px;line-height:25px;color:var(--ink);padding:0 60px}
.quote-name{font-size:17px;font-weight:600;color:var(--ink);margin-top:14px}
.quote-role{font-size:14px;color:var(--muted)}
.quote-arrows{margin-top:4px;color:var(--blue);font-size:16px;letter-spacing:6px}
.quote-badge{left:573px;top:170px;width:54px;height:54px;border-radius:50%;background:var(--blue);display:flex;align-items:center;justify-content:center}
/* cta */
.cta{top:3844px;height:340px;background:linear-gradient(180deg,#f4f5f7,#e9ebef)}
/* footer */
.footer{top:4183px;height:376px;background:var(--blue);color:#fff}
.footer h4{font-size:16px;font-weight:800;letter-spacing:.3px}
.footer h4::after{content:"";display:block;width:30px;height:2px;background:#fff;margin-top:10px}
.footer li{list-style:none;font-size:11.5px;margin-bottom:15px;color:#e6ebff}
.fitem{display:flex;gap:10px;margin-bottom:18px;font-size:11.5px}
.fitem b{display:block;font-size:12px}
.soc{display:flex;align-items:center;gap:10px;font-size:12px;margin-bottom:14px}
.soc i{width:24px;height:24px;border:1.5px solid #fff;border-radius:50%;display:block}
</style>
</head>
<body>

<div class="section topbar">
  <span><svg width="12" height="14" viewBox="0 0 12 14"><path d="M6 0a5 5 0 0 0-5 5c0 4 5 9 5 9s5-5 5-9a5 5 0 0 0-5-5zm0 7a2 2 0 1 1 0-4 2 2 0 0 1 0 4z" fill="#fff"/></svg>Location: <b>We're based in South Wales, UK.</b></span>
  <span><svg width="13" height="13" viewBox="0 0 24 24"><path d="M6.6 10.8a15 15 0 0 0 6.6 6.6l2.2-2.2a1 1 0 0 1 1-.25 11 11 0 0 0 3.6.6 1 1 0 0 1 1 1V20a1 1 0 0 1-1 1A17 17 0 0 1 3 4a1 1 0 0 1 1-1h3.5a1 1 0 0 1 1 1c0 1.25.2 2.45.6 3.6a1 1 0 0 1-.25 1z" fill="#fff"/></svg>Phone: <b>+44 (0) 7700 900418</b></span>
  <span><svg width="14" height="11" viewBox="0 0 14 11"><rect width="14" height="11" rx="1.5" fill="#fff"/><path d="M1 1.5l6 4.5 6-4.5" stroke="#3461f0" stroke-width="1.4" fill="none"/></svg>Email: <b>info@valtorix.design</b></span>
</div>

<div class="section header">
  <div class="abs brand" style="left:142px;top:13px">
    <div class="brand-dot"></div>
    <div><div class="brand-name">valtorix</div><div class="brand-sub">MECHANICAL DESIGN</div></div>
  </div>
  <div class="abs nav"><span class="active">Home</span><span>About Us</span><span>Services</span><span>Portfolio</span><span>Process</span></div>
  <div class="abs search"><svg width="15" height="15" viewBox="0 0 16 16"><circle cx="7" cy="7" r="5.5" stroke="#8a8f9a" stroke-width="1.5" fill="none"/><path d="M11 11l4 4" stroke="#8a8f9a" stroke-width="1.5"/></svg>Search...</div>
  <div class="abs contact-btn">Contact Us<span class="ring"><svg width="14" height="14" viewBox="0 0 24 24"><path d="M6.6 10.8a15 15 0 0 0 6.6 6.6l2.2-2.2a1 1 0 0 1 1-.25 11 11 0 0 0 3.6.6 1 1 0 0 1 1 1V20a1 1 0 0 1-1 1A17 17 0 0 1 3 4a1 1 0 0 1 1-1h3.5a1 1 0 0 1 1 1c0 1.25.2 2.45.6 3.6a1 1 0 0 1-.25 1z" fill="#2b2f36"/></svg></span></div>
</div>

<section class="section hero">
  <div class="abs hero-img" role="img" aria-label="Engineer at a desk working on a mechanical CAD model across two monitors"></div>
  <div class="abs hero-frame"></div>
  <h1>MECHANICAL<br>CAD DESIGN</h1>
  <div class="abs lead">Transforming concepts into production-ready designs<br>with expertise and innovation</div>
  <div class="abs btn">Start Your Project<span class="ring"><svg width="14" height="14" viewBox="0 0 24 24"><path d="M6.6 10.8a15 15 0 0 0 6.6 6.6l2.2-2.2a1 1 0 0 1 1-.25 11 11 0 0 0 3.6.6 1 1 0 0 1 1 1V20a1 1 0 0 1-1 1A17 17 0 0 1 3 4a1 1 0 0 1 1-1h3.5a1 1 0 0 1 1 1c0 1.25.2 2.45.6 3.6a1 1 0 0 1-.25 1z" fill="#3461f0"/></svg></span></div>
  <svg class="abs" style="left:0;top:480px" width="1200" height="180" viewBox="0 0 1200 180">
    <path d="M0 80 C300 40 520 50 700 90 C900 135 1080 150 1200 145 L1200 180 L0 180Z" fill="#5d7df2" opacity=".6"/>
    <path d="M0 80 C300 40 520 50 700 95 C880 140 1060 160 1200 170 L1200 180 L0 180Z" fill="#fff"/>
  </svg>
  <div class="abs" style="left:571px;top:514px;width:58px;height:58px;border-radius:50%;background:#fff;box-shadow:0 4px 14px rgba(0,0,0,.12);display:flex;align-items:center;justify-content:center">
    <svg width="22" height="30" viewBox="0 0 22 30"><rect x="1" y="1" width="20" height="28" rx="10" stroke="#3461f0" stroke-width="2" fill="none"/><path d="M11 8v12M7 16l4 4 4-4" stroke="#3461f0" stroke-width="2" fill="none"/></svg>
  </div>
</section>

<div class="abs about-img" role="img" aria-label="Designer working at a CAD workstation, shown inside a round blue frame"></div>
<div class="abs about-text">
  <div class="eyebrow">WHO WE ARE</div>
  <h2 class="title">Valtorix Mechanical Design</h2>
  <p>Welcome to Valtorix Mechanical Design. We are a UK based design consultancy offering a comprehensive mechanical and product design service from initial concepts through to full volume production.</p>
  <p>Duis autem vel eum iriure dolor in hendrerit in vulputate velit esse molestie consequat, vel illum dolore eu feugiat nulla facilisis at vero eros et accumsan et iusto odio dignissim qui blandit praesent luptatum zzril delenit augue duis dolore te feugait nulla facilisi tincidunt ut laoreet.</p>
  <div class="btn" style="width:128px;height:40px;margin-top:10px;font-size:12px">Read More</div>
</div>

<section class="section expertise">
  <div class="abs center eyebrow" style="top:88px">Solutions</div>
  <h2 class="abs center title" style="top:112px">Our Expertise</h2>
  <div class="abs card" style="left:142px"><div class="card-inner"></div><div style="position:relative">
    <div class="icon-c"><svg width="48" height="40" viewBox="0 0 48 40" fill="none" stroke="#3461f0" stroke-width="2"><path d="M2 12l10-6 8 4 6-3 10 4 10 5M6 20l10 10 4-2 6 6 4-2 6-6 8-6"/><path d="M20 10l-6 8 4 3 8-7"/></svg></div>
    <h3>Bespoke<br>Product Design</h3><p>Innovative design from concept through the full development life cycle</p></div></div>
  <div class="abs card featured" style="left:455px"><div class="card-inner"></div><div style="position:relative">
    <div class="icon-c"><svg width="44" height="44" viewBox="0 0 44 44" fill="none" stroke="#fff" stroke-width="2"><rect x="4" y="6" width="36" height="24" rx="2"/><path d="M16 38h12M22 30v8"/><path d="M22 11l7 4v8l-7 4-7-4v-8z"/></svg></div>
    <h3>3D Modelling and<br>Drawings</h3><p>We create 3D CAD, 2D engineering drawings and photorealistic renders</p></div></div>
  <div class="abs card" style="left:770px"><div class="card-inner"></div><div style="position:relative">
    <div class="icon-c"><svg width="44" height="40" viewBox="0 0 44 40" fill="none" stroke="#3461f0" stroke-width="2"><path d="M4 36V6h6v14l10-8v8l10-8v8l10-8v24z"/><path d="M12 28h4M20 28h4M28 28h4"/></svg></div>
    <h3>Design for<br>Manufacture</h3><p>Creating designs optimised for prototype and production manufacture</p></div></div>
</section>

<section class="section" style="top:1942px;height:708px">
  <div class="abs center eyebrow" style="top:88px">Projects</div>
  <h2 class="abs center title" style="top:112px">Our Portfolio</h2>
  <div class="abs center" style="top:158px;font-size:14.5px;color:var(--ink)">A small selection of our previous projects</div>
  <div class="abs slide" style="left:0;top:225px;width:362px;height:300px;background:radial-gradient(circle at 50% 50%,#9aa0a8 0%,#e3e5e8 32%,#ececee 100%)" role="img" aria-label="Render of a polished alloy wheel"></div>
  <div class="abs slide" style="left:386px;top:205px;width:428px;height:340px;background:radial-gradient(ellipse at 50% 60%,#c9a84a 0%,#8c8d90 25%,#e4e5e8 60%,#ededef 100%)" role="img" aria-label="Render of an action camera mounted on a threaded rail assembly"></div>
  <div class="abs slide" style="left:838px;top:225px;width:362px;height:300px;background:radial-gradient(circle at 45% 55%,#3a3c40 0%,#b0b3b8 35%,#ececee 100%)" role="img" aria-label="Render of a driving simulator seat frame"></div>
  <div class="abs" style="left:170px;top:601px;width:390px;height:1px;background:var(--line)"></div>
  <div class="abs" style="left:640px;top:601px;width:390px;height:1px;background:var(--line)"></div>
  <div class="abs" style="left:567px;top:588px;width:27px;height:27px;border-radius:50%;background:#8c8f96;display:flex;align-items:center;justify-content:center"><svg width="8" height="12" viewBox="0 0 8 12"><path d="M6 1L1.5 6 6 11" stroke="#fff" stroke-width="2" fill="none"/></svg></div>
  <div class="abs" style="left:604px;top:588px;width:27px;height:27px;border-radius:50%;background:var(--blue);display:flex;align-items:center;justify-content:center"><svg width="8" height="12" viewBox="0 0 8 12"><path d="M2 1l4.5 5L2 11" stroke="#fff" stroke-width="2" fill="none"/></svg></div>
</section>

<section class="section aboutme">
  <div class="abs" style="left:142px;top:112px;width:420px">
    <div class="eyebrow">About Me</div>
    <h2 class="title" style="margin:4px 0 12px">Ewan Marsh</h2>
    <p>Ewan Marsh is the Chief Engineer at Valtorix Mechanical Design. He has 11 years experience working as a mechanical design engineer in multiple industries including high performance automotive, consumer products, medical, industrial plus many more. He has worked in multiple roles across a wide range of products.</p>
    <p style="margin-top:12px">Ut wisi enim ad minim veniam, quis nostrud exerci t ullamcorper suscipit lobortis nisl ut aliquip ex ea commodo consequat. Duis autem vel eum iriure dolor in hendrerit.</p>
    <div class="btn" style="width:238px;height:42px;margin-top:22px;font-size:12px">Tell Us About Your Ideas</div>
  </div>
  <div class="abs" style="left:605px;top:93px;width:453px;height:408px;border-radius:10px;background:linear-gradient(160deg,#6f8a6e 0%,#4d5f55 45%,#2c3a55 100%)" role="img" aria-label="Portrait of the chief engineer"></div>
  <div class="abs" style="left:538px;top:378px;width:154px;height:154px;border-radius:50%;background:#fff;display:flex;align-items:center;justify-content:center"><div style="width:124px;height:124px;border-radius:50%;background:var(--blue)"></div></div>
</section>

<section class="section testimonials">
  <div class="abs center eyebrow" style="top:96px">Testimonials</div>
  <h2 class="abs center title" style="top:120px">Customer Reviews</h2>
  <div class="abs quote-card">
    <p class="quote-text">"Ewan is able to bridge the gap between what management want and what manufacturing can deliver.<br>In the field of Casting his intuition for the process and knowledge of casting technical nuances means he is able to push both the design and guide manufacturers to produce excellent results."</p>
    <div class="quote-name">Declan Royle</div>
    <div class="quote-role">Design Engineer</div>
    <div class="quote-arrows">&larr;&rarr;</div>
  </div>
  <div class="abs quote-badge"><svg width="26" height="20" viewBox="0 0 26 20"><path d="M2 12a8 8 0 0 1 8-10v4a4 4 0 0 0-3 4h3v8H2zM14 12a8 8 0 0 1 8-10v4a4 4 0 0 0-3 4h3v8h-8z" fill="#fff"/></svg></div>
</section>

<section class="section cta" role="img" aria-label="Faint engineering drawing background">
  <h2 class="abs center title" style="top:92px;font-size:30px">Curious What Else We Do?</h2>
  <p class="abs center" style="top:142px;color:var(--ink);font-size:14.5px;line-height:26px">Duis autem vel eum iriure dolor in hendrerit in vulputate velit esse molestie consequat,<br>vel illum dolore eu feugiat nulla facilisis at vero eros et accumsan.</p>
  <div class="abs btn" style="left:543px;top:222px;width:114px;height:40px;font-size:12px">See Here</div>
</section>

<footer class="section footer">
  <div class="abs" style="left:142px;top:68px">
    <h4>QUICK LINKS</h4>
    <ul style="margin-top:24px"><li>• Home</li><li>• About Us</li><li>• Our Services</li><li>• Portfolio</li><li>• Contact Us</li></ul>
  </div>
  <div class="abs" style="left:356px;top:68px">
    <h4>CONTACT DETAILS</h4>
    <div style="margin-top:24px">
      <div class="fitem"><svg width="12" height="14" viewBox="0 0 12 14"><path d="M6 0a5 5 0 0 0-5 5c0 4 5 9 5 9s5-5 5-9a5 5 0 0 0-5-5zm0 7a2 2 0 1 1 0-4 2 2 0 0 1 0 4z" fill="#fff"/></svg><div><b>ADDRESS</b>Millbank Lane, Cardiff, UK</div></div>
      <div class="fitem"><svg width="13" height="13" viewBox="0 0 24 24"><path d="M6.6 10.8a15 15 0 0 0 6.6 6.6l2.2-2.2a1 1 0 0 1 1-.25 11 11 0 0 0 3.6.6 1 1 0 0 1 1 1V20a1 1 0 0 1-1 1A17 17 0 0 1 3 4a1 1 0 0 1 1-1h3.5a1 1 0 0 1 1 1c0 1.25.2 2.450.6 3.6a1 1 0 0 1-.25 1z" fill="#fff"/></svg><div><b>PHONE</b>+44 (0)7700 900 418</div></div>
      <div class="fitem"><svg width="14" height="11" viewBox="0 0 14 11"><rect width="14" height="11" rx="1.5" fill="#fff"/><path d="M1 1.5l6 4.5 6-4.5" stroke="#3461f0" stroke-width="1.4" fill="none"/></svg><div><b>EMAIL</b>info@valtorix.design</div></div>
    </div>
  </div>
  <div class="abs" style="left:652px;top:68px">
    <h4>FOLLOW US</h4>
    <div style="margin-top:24px"><div class="soc"><i></i>Facebook</div><div class="soc"><i></i>Youtube</div><div class="soc"><i></i>Instagram</div><div class="soc"><i></i>Linkedin</div></div>
  </div>
  <div class="abs" style="left:858px;top:58px;width:200px;text-align:center">
    <div style="width:108px;height:108px;border-radius:50%;background:#fff;margin:0 auto 18px"></div>
    <div style="font-size:40px;font-weight:700;letter-spacing:4px;line-height:1">valtorix</div>
    <div style="font-size:14px;font-weight:700;letter-spacing:1.6px;margin-top:6px">MECHANICAL DESIGN</div>
  </div>
  <div class="abs" style="left:0;top:330px;width:1200px;height:1px;background:rgba(255,255,255,.25)"></div>
  <div class="abs center" style="top:345px;font-size:11px;color:#e6ebff">© 2025 Valtorix Mechanical Design. All Rights Reserved.</div>
</footer>

</body>
</html>
```